TL - business card

Tallow Partners is an insurance brokerage firm, inovative, proactive, vigorous, which aims to become the leader of the insurance brokers in Anfrica. We should like to get some designs which should be avoided also in Gray / Metallic for the Administration and Orange / Blue for the Managers (ike in the picture sent). The Blue / Green logo is not the correct one, but the source of the file. Please adjust the color accordingly for the business cards. 1 / Orange / Blue 2 / Gray / Metallic We want something classic but which is transmitted strenght, inovation, modernity and most of all, rapidity. We want something start-up like, very punchy and catching eye remaining profesional at the same time. Name: Dorian Whitlock Function: Managing Director Address: N ° 17/18 Rua Veloso - R / C 2B Direita - Bairro Mutamba - Luanda Tel: (+244) 947 582 316 Email: dorian.whitlock@tallow-p.example Website: www.tallow-p. example We want classic in the front and creative, colorfull at the back. The cards will be printed in relief, with very high quality of paper.
Insurance Broker
Colors
Designer to choose colors to be used in the design.

```html
<!DOCTYPE html>
<html lang="en">
<head>
<meta charset="utf-8">
<title>Tallow Partners – Business Card</title>
<link rel="stylesheet" href="https://fonts.googleapis.com/css2?family=Tinos&family=Open+Sans:wght@400;700&display=swap">
<style>
  :root {
    --page: #ffffff;
    --front-bg: #cecece;
    --back-bg: #3d3d3d;
    --frame-dark: #3f3f3f;
    --frame-light: #d2d2d2;
    --ink: #1e1e1e;
    --ink-soft: #3a3a3a;
    --blue: #3a87c9;
    --orange: #e57f43;
    --ghost-front: #c4c4c4;
    --ghost-back: #4c4c4c;
  }
  * { margin: 0; padding: 0; box-sizing: border-box; }
  html, body { width: 1031px; height: 1200px; overflow: hidden; background: var(--page); }
  .canvas { position: relative; width: 1031px; height: 1200px; }

  .card { position: absolute; width: 958px; height: 547px; overflow: hidden; }
  .card--front { left: 36px; top: 32px; background: var(--front-bg); }
  .card--back { left: 35px; top: 616px; background: var(--back-bg); }

  .frame { position: absolute; }
  .card--front .frame--outer { left: 25px; top: 29px; width: 904px; height: 489px; border: 4px solid var(--frame-dark); }
  .card--front .frame--inner { left: 39px; top: 42px; width: 878px; height: 464px; border: 3px solid var(--frame-dark); }
  .card--back .frame--outer { left: 26px; top: 29px; width: 904px; height: 489px; border: 4px solid var(--frame-light); }
  .card--back .frame--inner { left: 40px; top: 41px; width: 878px; height: 465px; border: 3px solid var(--frame-light); }

  .ghost-ring { position: absolute; border-radius: 50%; }
  .card--front .ghost-ring { left: 101px; top: 123px; width: 300px; height: 300px; border: 26px solid var(--ghost-front); }

  .person { position: absolute; left: 80px; top: 126px; font-family: "Tinos", serif; }
  .person__name { font-size: 51px; line-height: 1; color: var(--blue); font-weight: 400; }
  .person__role { margin: 8px 0 0 8px; font-size: 22px; color: var(--ink-soft); letter-spacing: 0.3px; }

  .contacts { position: absolute; left: 79px; top: 254px; list-style: none; font-family: "Open Sans", sans-serif; font-size: 20px; color: var(--ink); }
  .contact { position: relative; padding-left: 54px; min-height: 40px; display: flex; align-items: center; line-height: 25px; }
  .contact + .contact { margin-top: 14px; }
  .contact__icon { position: absolute; left: 0; top: 50%; width: 40px; height: 40px; margin-top: -20px; }
  .contact--address { margin-top: 16px; }

  .divider { position: absolute; left: 478px; top: 208px; width: 2px; height: 148px; background: var(--ink); }

  .brand { position: absolute; left: 567px; top: 214px; width: 280px; text-align: center; }
  .brand__dot { display: block; margin: 0 auto 14px; width: 92px; height: 92px; border-radius: 50%; border: 9px solid var(--orange); }
  .brand__name { font-family: "Open Sans", sans-serif; font-weight: 700; font-size: 27px; line-height: 1.1; color: var(--orange); letter-spacing: 0.3px; white-space: nowrap; }

  .website { position: absolute; left: 0; width: 100%; top: 462px; line-height: 26px; text-align: center; font-family: "Tinos", serif; font-size: 22px; color: var(--ink); letter-spacing: 0.5px; }
  .website__domain { color: var(--blue); }

  .pattern { position: absolute; inset: 0; }
  .pattern__ring { position: absolute; width: 94px; height: 94px; margin: -47px 0 0 -47px; border-radius: 50%; border: 9px solid var(--ghost-back); }
  .emblem { position: absolute; left: 480px; top: 276px; transform: translate(-50%, -50%); text-align: center; }
  .emblem__dot { display: block; margin: 0 auto 10px; width: 94px; height: 94px; border-radius: 50%; border: 9px solid var(--orange); }
  .emblem__name { font-family: "Open Sans", sans-serif; font-weight: 700; font-size: 15px; color: var(--blue); white-space: nowrap; }
</style>
</head>
<body>
<main class="canvas">

  <section class="card card--front" aria-label="Business card front">
    <div class="frame frame--outer"></div>
    <div class="frame frame--inner"></div>
    <div class="ghost-ring" aria-hidden="true"></div>

    <header class="person">
      <h1 class="person__name">Dorian Whitlock</h1>
      <p class="person__role">Managing Director</p>
    </header>

    <ul class="contacts">
      <li class="contact contact--phone">
        <svg class="contact__icon" viewBox="0 0 40 40" aria-hidden="true">
          <path d="M20 3 A17 17 0 1 0 37 20" fill="none" stroke="var(--blue)" stroke-width="2.5"/>
          <path d="M13 11 l4 -1 l3 6 l-3 2 q2 5 7 7 l2 -3 l6 3 l-1 4 q-10 1 -18 -18 z" fill="none" stroke="var(--blue)" stroke-width="2" stroke-linejoin="round"/>
        </svg>
        <span>(+244) 947 582 316</span>
      </li>
      <li class="contact contact--email">
        <svg class="contact__icon" viewBox="0 0 40 40" aria-hidden="true">
          <path d="M20 3 A17 17 0 1 0 37 20" fill="none" stroke="var(--blue)" stroke-width="2.5"/>
          <rect x="11" y="14" width="18" height="13" rx="2" fill="var(--blue)"/>
          <path d="M11 15 l9 7 l9 -7" fill="none" stroke="var(--front-bg)" stroke-width="2"/>
        </svg>
        <span>dorian.whitlock@tallow-p.example</span>
      </li>
      <li class="contact contact--address">
        <svg class="contact__icon" viewBox="0 0 40 40" aria-hidden="true">
          <path d="M20 3 A17 17 0 1 0 37 20" fill="none" stroke="var(--blue)" stroke-width="2.5"/>
          <path d="M20 31 C14 24 12 20 12 17 a8 8 0 0 1 16 0 c0 3 -2 7 -8 14 z" fill="none" stroke="var(--blue)" stroke-width="2.2"/>
          <circle cx="20" cy="17" r="3" fill="var(--blue)"/>
        </svg>
        <span>N° 17/18 Rua Veloso - R / C 2B<br>Direita-Bairro Mutamba-Luanda</span>
      </li>
    </ul>

    <div class="divider" aria-hidden="true"></div>

    <div class="brand">
      <span class="brand__dot" aria-hidden="true"></span>
      <p class="brand__name">TALLOW PARTNERS</p>
    </div>

    <p class="website">www.<span class="website__domain">tallow-p</span>.example</p>
  </section>

  <section class="card card--back" aria-label="Business card back">
    <div class="frame frame--outer"></div>
    <div class="frame frame--inner"></div>
    <div class="pattern" aria-hidden="true">
      <span class="pattern__ring" style="left:115px;top:127px"></span>
      <span class="pattern__ring" style="left:293px;top:127px"></span>
      <span class="pattern__ring" style="left:480px;top:127px"></span>
      <span class="pattern__ring" style="left:667px;top:127px"></span>
      <span class="pattern__ring" style="left:836px;top:127px"></span>
      <span class="pattern__ring" style="left:115px;top:276px"></span>
      <span class="pattern__ring" style="left:293px;top:276px"></span>
      <span class="pattern__ring" style="left:667px;top:276px"></span>
      <span class="pattern__ring" style="left:836px;top:276px"></span>
      <span class="pattern__ring" style="left:115px;top:424px"></span>
      <span class="pattern__ring" style="left:293px;top:424px"></span>
      <span class="pattern__ring" style="left:480px;top:424px"></span>
      <span class="pattern__ring" style="left:667px;top:424px"></span>
      <span class="pattern__ring" style="left:836px;top:424px"></span>
    </div>
    <div class="emblem">
      <span class="emblem__dot" aria-hidden="true"></span>
      <p class="emblem__name">Tallow Partners</p>
    </div>
  </section>

</main>
</body>
</html>
```